PowerPoint Design for upcoming Broadcast

I need a PowerPoint design complete with all the templates in PPT, i.e two columns of text, one column of text with adjacent area for image, etc. Per the attached logo. Do not use the gold element in the design. 16x9

Target Market(s)

Business Leaders

Industry/Entity Type

Business Consultant

Other font styles liked:
• Arial

Colors

Designer to choose colors to be used in the design.

Requirements
Must have
• Crisp clean design. #for each color used.
Nice to have
• An assortment of charts in the ppt color schemes. A military (KVTF) theme.
Should not have
• Gaudy. Flashy. Transitions.

```html
<!DOCTYPE html>
<html lang="en">
<head>
<meta charset="utf-8">
<title>KVTF Broadcast Deck – Slide Overview</title>
<link href="https://fonts.googleapis.com/css2?family=Tinos:wght@400;700&display=swap" rel="stylesheet">
<style>
  :root{
    --red:#a30d12;
    --ink:#1e1e1e;
    --grey:#7b7b7b;
    --mist:#cfcfcf;
    --paper:#ffffff;
    --fine:#8a8a8a;
    --desk:#f3f3f3;
  }
  html,body{margin:0;padding:0;width:898px;height:1200px;overflow:hidden;background:var(--desk);}
  .deck{position:relative;width:898px;height:1200px;}
  .slide{position:absolute;width:296px;height:166px;background:var(--paper);box-shadow:0 1px 3px rgba(0,0,0,.25);overflow:hidden;}
  .slide svg{display:block;width:296px;height:166px;font-family:Tinos,"Times New Roman",serif;}
  .c1{left:2px}.c2{left:301px}.c3{left:600px}
  .r1{top:4px}.r2{top:175px}.r3{top:346px}.r4{top:517px}.r5{top:688px}.r6{top:859px}.r7{top:1030px}
  .title{font-size:9px;fill:var(--ink);letter-spacing:.2px}
  .head{font-size:4.4px;fill:var(--ink)}
  .head-red{font-size:4.4px;fill:var(--red)}
  .big{font-size:6.5px;fill:#555}
  .fine{font-size:2.3px;fill:var(--fine)}
  .fine-w{font-size:2.3px;fill:#eee}
  .tiny{font-size:2.8px;fill:#555}
  .label-w{font-size:3.4px;fill:#fff}
  .num{font-size:10px;fill:#555}
  .foot-text{font-size:2.2px;fill:#ddd}
  .accent{fill:var(--red)}
  .ink{fill:var(--ink)}
  .grey{fill:var(--grey)}
  .mist{fill:var(--mist)}
</style>
</head>
<body>
<main class="deck">

<!-- Row 1 -->
<section class="slide c1 r1" aria-label="Timeline opening slide">
  <svg viewBox="0 0 296 166">
    <defs><linearGradient id="topband" x1="0" y1="0" x2="0" y2="1"><stop offset="0" stop-color="#2a2a2a"/><stop offset="1" stop-color="#151515"/></linearGradient></defs>
    <rect width="296" height="78" fill="url(#topband)"/>
    <circle cx="134" cy="30" r="5" class="accent"/>
    <text x="143" y="33.5" font-size="10" fill="#fff">KVTF</text>
    <text x="148" y="62" text-anchor="middle" font-size="8" fill="#fff">This Is Your Timeline Page</text>
    <text x="148" y="90" text-anchor="middle" class="head">Your Heading Here</text>
    <text x="148" y="96" text-anchor="middle" class="fine">Lorem ipsum dolor sit amet, consectetur adipiscing elit, sed do eiusmod</text>
    <text x="148" y="99.5" text-anchor="middle" class="fine">tempor incididunt ut labore et dolore magna aliqua. Ut enim ad minim</text>
    <text x="148" y="103" text-anchor="middle" class="fine">veniam, quis nostrud exercitation ullamco laboris nisi ut aliquip</text>
    <line x1="148" y1="146" x2="148" y2="166" stroke="#bbb" stroke-width=".6"/>
    <circle cx="148" cy="146" r="3" class="ink"/>
  </svg>
</section>

<section class="slide c2 r1" aria-label="Your title with image slide">
  <svg viewBox="0 0 296 166">
    <defs><linearGradient id="sandphoto" x1="0" y1="0" x2="1" y2="1"><stop offset="0" stop-color="#d9d3cc"/><stop offset=".6" stop-color="#a89684"/><stop offset="1" stop-color="#e6e1dc"/></linearGradient></defs>
    <rect x="8" y="11" width="1.2" height="12" class="accent"/>
    <text x="13" y="20.5" class="title">YOUR TITLE</text>
    <rect x="150" y="0" width="146" height="82" fill="url(#sandphoto)" role="img" aria-label="Photo of soldiers advancing across sand"/>
    <rect x="20" y="35" width="4" height="4" transform="rotate(45 22 37)" fill="none" stroke="#555" stroke-width=".7"/>
    <text x="29" y="38.5" class="head">Bullet Point</text>
    <text x="29" y="43" class="fine">Lorem ipsum dolor sit amet, consectetur adipiscing elit, sed</text>
    <text x="29" y="46" class="fine">do eiusmod tempor incididunt ut labore et dolore magna</text>
    <text x="29" y="49" class="fine">aliqua enim</text>
    <rect x="0" y="82" width="150" height="84" fill="#6c6c6c"/>
    <text x="10" y="103" class="fine-w">Lorem ipsum dolor sit amet, consectetur adipiscing elit, sed do eiusmod</text>
    <text x="10" y="106.5" class="fine-w">tempor incididunt ut labore et dolore magna aliqua. Ut enim ad minim</text>
    <text x="10" y="110" class="fine-w">veniam, quis nostrud exercitation ullamco laboris nisi ut aliquip.</text>
    <text x="10" y="116" class="fine-w">Duis aute irure dolor in reprehenderit in voluptate velit esse cillum</text>
    <text x="10" y="119.5" class="fine-w">dolore eu fugiat nulla pariatur excepteur.</text>
    <rect x="165" y="113" width="6" height="4" fill="none" stroke="#999" stroke-width=".5"/>
    <text x="176" y="117" class="head">Bullet Point</text>
    <text x="176" y="121.5" class="fine">Lorem ipsum dolor sit amet, consectetur adipiscing elit, sed</text>
    <text x="176" y="124.5" class="fine">do eiusmod tempor incididunt ut labore et dolore magna</text>
    <text x="176" y="127.5" class="fine">aliqua enim</text>
    <text x="290" y="162" text-anchor="end" class="fine">44</text>
  </svg>
</section>

<section class="slide c3 r1" aria-label="Your title with three bullets slide">
  <svg viewBox="0 0 296 166">
    <defs><linearGradient id="dunephoto" x1="0" y1="0" x2="0" y2="1"><stop offset="0" stop-color="#6b5a4b"/><stop offset=".7" stop-color="#b59678"/><stop offset="1" stop-color="#8f735a"/></linearGradient></defs>
    <rect x="8" y="11" width="1.2" height="12" class="accent"/>
    <text x="13" y="20.5" class="title">YOUR TITLE</text>
    <rect x="148" y="0" width="148" height="92" fill="url(#dunephoto)" role="img" aria-label="Photo of a soldier in a desert"/>
    <rect x="148" y="92" width="148" height="68" fill="#1b1b1b"/>
    <text x="160" y="104" class="fine-w">Lorem ipsum dolor sit amet, consectetur adipiscing elit, sed do</text>
    <text x="160" y="107.5" class="fine-w">eiusmod tempor incididunt ut labore et dolore magna aliqua. Ut</text>
    <text x="160" y="111" class="fine-w">enim ad minim veniam, quis nostrud exercitation ullamco.</text>
    <text x="160" y="117" class="fine-w">Duis aute irure dolor in reprehenderit in voluptate velit esse</text>
    <text x="160" y="120.5" class="fine-w">cillum dolore eu fugiat nulla pariatur excepteur.</text>
    <rect x="17" y="39" width="4" height="4" transform="rotate(45 19 41)" fill="none" stroke="#555" stroke-width=".7"/>
    <text x="28" y="43" class="head">Bullet Point</text>
    <text x="28" y="47.5" class="fine">Lorem ipsum dolor sit amet, consectetur adipiscing elit, sed</text>
    <text x="28" y="50.5" class="fine">do eiusmod tempor incididunt ut labore et dolore magna</text>
    <rect x="16" y="79" width="1.2" height="4" class="accent"/><rect x="18" y="77" width="1.2" height="6" class="accent"/><rect x="20" y="80" width="1.2" height="3" class="accent"/>
    <text x="28" y="82" class="head-red">Chart</text>
    <text x="28" y="86.5" class="fine">Lorem ipsum dolor sit amet, consectetur adipiscing elit, sed</text>
    <text x="28" y="89.5" class="fine">do eiusmod tempor incididunt ut labore et dolore magna</text>
    <circle cx="16.5" cy="119" r="1" fill="#777"/><circle cx="20.5" cy="116.5" r="1" fill="#777"/><circle cx="20.5" cy="121.5" r="1" fill="#777"/>
    <path d="M16.5 119 L20.5 116.5 M16.5 119 L20.5 121.5" stroke="#777" stroke-width=".4"/>
    <text x="28" y="122" class="head">Share</text>
    <text x="28" y="126.5" class="fine">Lorem ipsum dolor sit amet, consectetur adipiscing elit, sed</text>
    <text x="28" y="129.5" class="fine">do eiusmod tempor incididunt ut labore et dolore magna</text>
    <rect y="160" width="296" height="6" class="ink"/><circle cx="6" cy="163" r="2.4" class="accent"/>
    <text x="11" y="164" class="foot-text">© Copyright 2018 KVTF. All rights reserved</text>
  </svg>
</section>

<!-- Row 2 -->
<section class="slide c1 r2" aria-label="Timeline middle slide">
  <svg viewBox="0 0 296 166">
    <line x1="148" y1="0" x2="148" y2="166" stroke="#ccc" stroke-width=".6"/>
    <circle cx="148" cy="21" r="3" class="ink"/><circle cx="148" cy="49" r="3" class="ink"/><circle cx="148" cy="108" r="3" class="ink"/>
    <text x="130" y="23" text-anchor="end" class="tiny">You Title</text>
    <text x="130" y="28" text-anchor="end" class="fine">Duis aute irure dolor in reprehenderit in voluptate velit esse cillum</text>
    <text x="130" y="31" text-anchor="end" class="fine">dolore eu fugiat nulla pariatur excepteur</text>
    <text x="162" y="58" class="tiny">You Title</text>
    <text x="162" y="69" class="num">85%</text>
    <text x="162" y="74" class="fine">Duis aute irure dolor in reprehenderit in voluptate velit</text>
    <text x="162" y="77" class="fine">esse cillum dolore eu fugiat nulla</text>
    <text x="130" y="110" text-anchor="end" class="tiny">You Title</text>
    <rect x="60" y="113" width="72" height="18" class="accent"/>
    <text x="96" y="119" text-anchor="middle" class="fine-w">Duis aute irure dolor in reprehenderit in</text>
    <text x="96" y="122.5" text-anchor="middle" class="fine-w">voluptate velit esse cillum dolore eu</text>
    <text x="96" y="126" text-anchor="middle" class="fine-w">fugiat nulla pariatur</text>
  </svg>
</section>

<section class="slide c2 r2" aria-label="Who we are slide">
  <svg viewBox="0 0 296 166">
    <rect x="8" y="11" width="1.2" height="12" class="accent"/>
    <text x="13" y="20.5" class="title">WHO WE ARE?</text>
    <g>
      <text x="22" y="43" class="big">A Title About</text><text x="22" y="51" class="big">Contents</text>
      <text x="22" y="56" class="fine">Lorem ipsum dolor sit</text>
      <text x="90" y="39" class="fine">2017</text><line x1="90" y1="41" x2="272" y2="41" stroke="#333" stroke-width=".5"/>
      <text x="90" y="46" class="fine">Lorem ipsum dolor sit amet, consectetur adipiscing elit, sed do eiusmod tempor incididunt ut labore</text>
      <text x="90" y="49.5" class="fine">et dolore aliqua. Lorem ipsum dolor sit amet, consectetur adipiscing elit, sed do eiusmod tempor</text>
      <text x="90" y="53" class="fine">incididunt ut labore</text>
    </g>
    <g>
      <text x="22" y="81" class="big" fill="#a30d12" style="fill:var(--red)">A Title About</text><text x="22" y="89" style="fill:var(--red)" class="big">Contents</text>
      <text x="22" y="94" class="fine" style="fill:var(--red)">Lorem ipsum dolor sit</text>
      <text x="90" y="77" class="fine">2018</text><line x1="90" y1="79" x2="272" y2="79" stroke="#a30d12" stroke-width=".5"/>
      <text x="90" y="84" class="fine">Lorem ipsum dolor sit amet, consectetur adipiscing elit, sed do eiusmod tempor incididunt ut labore</text>
      <text x="90" y="87.5" class="fine">et dolore aliqua. Lorem ipsum dolor sit amet, consectetur adipiscing elit, sed do eiusmod tempor</text>
      <text x="90" y="91" class="fine">incididunt ut labore</text>
    </g>
    <g>
      <text x="22" y="119" class="big" style="fill:#888">A Title About</text><text x="22" y="127" class="big" style="fill:#888">Contents</text>
      <text x="22" y="132" class="fine">Lorem ipsum dolor sit</text>
      <text x="90" y="115" class="fine">2019</text><line x1="90" y1="117" x2="272" y2="117" stroke="#888" stroke-width=".5"/>
      <text x="90" y="122" class="fine">Lorem ipsum dolor sit amet, consectetur adipiscing elit, sed do eiusmod tempor incididunt ut labore</text>
      <text x="90" y="125.5" class="fine">et dolore aliqua. Lorem ipsum dolor sit amet, consectetur adipiscing elit, sed do eiusmod tempor</text>
      <text x="90" y="129" class="fine">incididunt ut labore</text>
    </g>
    <rect y="160" width="296" height="6" class="ink"/><circle cx="6" cy="163" r="2.4" class="accent"/>
    <text x="11" y="164" class="foot-text">© Copyright 2018 KVTF. All rights reserved</text>
  </svg>
</section>

<section class="slide c3 r2" aria-label="Bullet and pie chart slide">
  <svg viewBox="0 0 296 166">
    <rect x="8" y="11" width="1.2" height="12" class="accent"/>
    <text x="13" y="20.5" class="title">BULLET &amp; CHART AREA</text>
    <path d="M70 85 L70 55 A30 30 0 1 1 52.4 109.3 Z" class="ink"/>
    <path d="M70 85 L52.4 109.3 A30 30 0 0 1 41.5 75.7 Z" class="accent"/>
    <path d="M70 85 L41.5 75.7 A30 30 0 0 1 60.7 56.5 Z" class="grey"/>
    <path d="M70 85 L60.7 56.5 A30 30 0 0 1 70 55 Z" fill="#e6e6e6" stroke="#999" stroke-width=".3"/>
    <text x="58" y="50" class="big">10%</text>
    <text x="28" y="66" class="big">15%</text>
    <text x="26" y="113" class="big" style="fill:var(--red)">25%</text>
    <text x="106" y="93" class="big">60%</text>
    <text x="52" y="125" class="fine">● 1st Qtr  ● 2nd Qtr  ● 3rd Qtr  ● 4th Qtr</text>
    <g>
      <circle cx="165" cy="49" r="5" class="ink"/><circle cx="164.3" cy="48.3" r="1.6" fill="none" stroke="#fff" stroke-width=".6"/>
      <text x="175" y="48" class="tiny">Category One</text>
      <text x="175" y="52" class="fine">Lorem ipsum dolor sit amet, consectetur adipiscing</text>
      <circle cx="165" cy="73" r="5" class="accent"/><path d="M163 75 L167 71" stroke="#fff" stroke-width=".8"/>
      <text x="175" y="72" class="tiny" style="fill:var(--red)">Category Two</text>
      <text x="175" y="76" class="fine">Lorem ipsum dolor sit amet, consectetur adipiscing</text>
      <circle cx="165" cy="97" r="5" class="grey"/><path d="M163 99 L167 95" stroke="#fff" stroke-width=".8"/>
      <text x="175" y="96" class="tiny">Category Three</text>
      <text x="175" y="100" class="fine">Lorem ipsum dolor sit amet, consectetur adipiscing</text>
      <circle cx="165" cy="121" r="5" class="ink"/><circle cx="165" cy="121" r="1.8" fill="none" stroke="#fff" stroke-width=".8"/>
      <text x="175" y="120" class="tiny">Category Four</text>
      <text x="175" y="124" class="fine">Lorem ipsum dolor sit amet, consectetur adipiscing</text>
    </g>
    <rect y="160" width="296" height="6" class="ink"/><circle cx="6" cy="163" r="2.4" class="accent"/>
    <text x="11" y="164" class="foot-text">© Copyright 2018 KVTF. All rights reserved</text>
  </svg>
</section>

<!-- Row 3 -->
<section class="slide c1 r3" aria-label="Timeline closing slide">
  <svg viewBox="0 0 296 166">
    <line x1="148" y1="0" x2="148" y2="140" stroke="#ccc" stroke-width=".6"/>
    <circle cx="148" cy="28" r="3" class="ink"/><circle cx="148" cy="55" r="3" class="ink"/><circle cx="148" cy="100" r="3" class="ink"/>
    <text x="162" y="33" font-size="7" class="ink">Your</text>
    <text x="162" y="42" font-size="7" class="ink">Title Here</text>
    <text x="130" y="56" text-anchor="end" class="tiny">Timeline</text>
    <text x="130" y="61" text-anchor="end" class="tiny">Finish</text>
    <text x="162" y="56" class="fine">Duis aute irure dolor in reprehenderit in voluptate velit esse cillum</text>
    <text x="162" y="59" class="fine">dolore eu fugiat nulla pariatur excepteur</text>
    <text x="100" y="75" text-anchor="end" class="fine">Duis aute irure dolor in reprehenderit in</text>
    <text x="100" y="78" text-anchor="end" class="fine">voluptate velit esse cillum dolore eu</text>
    <text x="130" y="81" text-anchor="end" class="num">50%</text>
    <text x="162" y="102" class="tiny">You Title</text>
    <text x="162" y="107" class="fine">Duis aute irure dolor in reprehenderit in voluptate velit esse</text>
    <text x="162" y="110" class="fine">cillum dolore eu fugiat nulla pariatur</text>
    <circle cx="132" cy="140" r="5" class="accent"/>
    <text x="141" y="143.5" font-size="10" class="ink">KVTF</text>
  </svg>
</section>

<section class="slide c2 r3" aria-label="Bullet and horizontal bar chart slide">
  <svg viewBox="0 0 296 166">
    <rect x="8" y="11" width="1.2" height="12" class="accent"/>
    <text x="13" y="20.5" class="title">BULLET &amp; CHART AREA</text>
    <g>
      <text x="22" y="55" class="fine">Category 4</text>
      <rect x="41" y="48" width="81" height="3" class="ink"/><rect x="41" y="51.5" width="60" height="3" class="accent"/><rect x="41" y="55" width="70" height="3" class="grey"/>
      <text x="22" y="80" class="fine">Category 3</text>
      <rect x="41" y="73" width="32" height="3" class="ink"/><rect x="41" y="76.5" width="67" height="3" class="accent"/><rect x="41" y="80" width="50" height="3" class="grey"/>
      <text x="22" y="103" class="fine">Category 2</text>
      <rect x="41" y="96" width="40" height="3" class="ink"/><rect x="41" y="99.5" width="72" height="3" class="accent"/><rect x="41" y="103" width="36" height="3" class="grey"/>
      <text x="22" y="126" class="fine">Category 1</text>
      <rect x="41" y="119" width="38" height="3" class="ink"/><rect x="41" y="122.5" width="26" height="3" class="accent"/><rect x="41" y="126" width="74" height="3" class="grey"/>
      <text x="60" y="136" class="fine">● Series 1  ● Series 2  ● Series 3</text>
    </g>
    <g>
      <circle cx="165" cy="49" r="5" class="ink"/><circle cx="164.3" cy="48.3" r="1.6" fill="none" stroke="#fff" stroke-width=".6"/>
      <text x="175" y="48" class="tiny">Category One</text>
      <text x="175" y="52" class="fine">Lorem ipsum dolor sit amet, consectetur adipiscing</text>
      <circle cx="165" cy="73" r="5" class="accent"/><path d="M163 75 L167 71" stroke="#fff" stroke-width=".8"/>
      <text x="175" y="72" class="tiny" style="fill:var(--red)">Category Two</text>
      <text x="175" y="76" class="fine">Lorem ipsum dolor sit amet, consectetur adipiscing</text>
      <circle cx="165" cy="97" r="5" class="grey"/><path d="M163 99 L167 95" stroke="#fff" stroke-width=".8"/>
      <text x="175" y="96" class="tiny">Category Three</text>
      <text x="175" y="100" class="fine">Lorem ipsum dolor sit amet, consectetur adipiscing</text>
      <circle cx="165" cy="121" r="5" class="ink"/><circle cx="165" cy="121" r="1.8" fill="none" stroke="#fff" stroke-width=".8"/>
      <text x="175" y="120" class="tiny">Category Four</text>
      <text x="175" y="124" class="fine">Lorem ipsum dolor sit amet, consectetur adipiscing</text>
    </g>
    <rect y="160" width="296" height="6" class="ink"/><circle cx="6" cy="163" r="2.4" class="accent"/>
    <text x="11" y="164" class="foot-text">© Copyright 2018 KVTF. All rights reserved</text>
  </svg>
</section>

<section class="slide c3 r3" aria-label="Bullet and column chart slide">
  <svg viewBox="0 0 296 166">
    <rect x="8" y="11" width="1.2" height="12" class="accent"/>
    <text x="13" y="20.5" class="title">BULLET &amp; CHART AREA</text>
    <g>
      <circle cx="36" cy="46" r="5" class="ink"/><circle cx="35.3" cy="45.3" r="1.6" fill="none" stroke="#fff" stroke-width=".6"/>
      <text x="47" y="45" class="tiny">You Text Here</text>
      <text x="47" y="49" class="fine">Lorem ipsum dolor sit amet, consectetur adipiscing elit</text>
      <circle cx="36" cy="70" r="5" class="accent"/><path d="M34 72 L38 68" stroke="#fff" stroke-width=".8"/>
      <text x="47" y="69" class="tiny" style="fill:var(--red)">You Text Here</text>
      <text x="47" y="73" class="fine">Lorem ipsum dolor sit amet, consectetur adipiscing elit</text>
      <circle cx="36" cy="94" r="5" class="grey"/><path d="M34 96 L38 92" stroke="#fff" stroke-width=".8"/>
      <text x="47" y="93" class="tiny">You Text Here</text>
      <text x="47" y="97" class="fine">Lorem ipsum dolor sit amet, consectetur adipiscing elit</text>
      <circle cx="36" cy="118" r="5" class="ink"/><circle cx="36" cy="118" r="1.8" fill="none" stroke="#fff" stroke-width=".8"/>
      <text x="47" y="117" class="tiny">You Text Here</text>
      <text x="47" y="121" class="fine">Lorem ipsum dolor sit amet, consectetur adipiscing elit</text>
    </g>
    <g>
      <rect x="199" y="64" width="4" height="50" class="ink"/><rect x="204" y="88" width="4" height="26" class="accent"/><rect x="209" y="94" width="4" height="20" class="grey"/>
      <rect x="228" y="88" width="4" height="26" class="ink"/><rect x="233" y="63" width="4" height="51" class="accent"/><rect x="238" y="92" width="4" height="22" class="grey"/>
      <rect x="257" y="80" width="4" height="34" class="ink"/><rect x="262" y="98" width="4" height="16" class="accent"/><rect x="267" y="84" width="4" height="30" class="grey"/>
      <rect x="286" y="56" width="4" height="58" class="ink"/>
      <line x1="195" y1="114" x2="292" y2="114" stroke="#bbb" stroke-width=".3"/>
      <text x="206" y="119" text-anchor="middle" class="fine">Category 1</text>
      <text x="235" y="119" text-anchor="middle" class="fine">Category 2</text>
      <text x="264" y="119" text-anchor="middle" class="fine">Category 3</text>
      <text x="232" y="124" class="fine">● Series 1  ● Series 2  ● Series 3</text>
    </g>
    <rect y="160" width="296" height="6" class="ink"/><circle cx="6" cy="163" r="2.4" class="accent"/>
    <text x="11" y="164" class="foot-text">© Copyright 2018 KVTF. All rights reserved</text>
  </svg>
</section>

<!-- Row 4 -->
<section class="slide c1 r4" aria-label="Column chart slide">
  <svg viewBox="0 0 296 166">
    <rect x="8" y="11" width="1.2" height="12" class="accent"/>
    <text x="13" y="20.5" class="title">COLUMN CHART</text>
    <g class="values">
      <rect x="26" y="45" width="12" height="70" class="ink"/><rect x="39" y="72" width="12" height="43" class="accent"/><rect x="52" y="86" width="12" height="29" class="grey"/>
      <text x="32" y="43" text-anchor="middle" class="fine">49</text><text x="45" y="70" text-anchor="middle" class="fine" style="fill:var(--red)">30</text><text x="58" y="84" text-anchor="middle" class="fine">20</text>
      <rect x="96" y="79" width="12" height="36" class="ink"/><rect x="109" y="52" width="12" height="63" class="accent"/><rect x="122" y="84" width="12" height="31" class="grey"/>
      <text x="102" y="77" text-anchor="middle" class="fine">25</text><text x="115" y="50" text-anchor="middle" class="fine" style="fill:var(--red)">44</text><text x="128" y="82" text-anchor="middle" class="fine">22</text>
      <rect x="164" y="63" width="12" height="52" class="ink"/><rect x="177" y="89" width="12" height="26" class="accent"/><rect x="190" y="51" width="12" height="64" class="grey"/>
      <text x="170" y="61" text-anchor="middle" class="fine">36</text><text x="183" y="87" text-anchor="middle" class="fine" style="fill:var(--red)">18</text><text x="196" y="49" text-anchor="middle" class="fine">45</text>
      <rect x="232" y="38" width="12" height="77" class="ink"/><rect x="245" y="75" width="12" height="40" class="accent"/><rect x="258" y="68" width="12" height="47" class="grey"/>
      <text x="238" y="36" text-anchor="middle" class="fine">54</text><text x="251" y="73" text-anchor="middle" class="fine" style="fill:var(--red)">28</text><text x="264" y="66" text-anchor="middle" class="fine">33</text>
    </g>
    <text x="45" y="121" text-anchor="middle" class="fine">Category 1</text>
    <text x="45" y="125" text-anchor="middle" class="fine">Lorem ipsum dolor sit amet,</text>
    <text x="45" y="128" text-anchor="middle" class="fine">consectetur adipiscing elit</text>
    <text x="115" y="121" text-anchor="middle" class="fine">Category 2</text>
    <text x="115" y="125" text-anchor="middle" class="fine">Lorem ipsum dolor sit amet,</text>
    <text x="115" y="128" text-anchor="middle" class="fine">consectetur adipiscing elit</text>
    <text x="183" y="121" text-anchor="middle" class="fine">Category 3</text>
    <text x="183" y="125" text-anchor="middle" class="fine">Lorem ipsum dolor sit amet,</text>
    <text x="183" y="128" text-anchor="middle" class="fine">consectetur adipiscing elit</text>
    <text x="251" y="121" text-anchor="middle" class="fine">Category 4</text>
    <text x="251" y="125" text-anchor="middle" class="fine">Lorem ipsum dolor sit amet,</text>
    <text x="251" y="128" text-anchor="middle" class="fine">consectetur adipiscing elit</text>
    <rect y="160" width="296" height="6" class="ink"/><circle cx="6" cy="163" r="2.4" class="accent"/>
    <text x="11" y="164" class="foot-text">© Copyright 2018 KVTF. All rights reserved</text>
  </svg>
</section>

<section class="slide c2 r4" aria-label="Bar chart slide">
  <svg viewBox="0 0 296 166">
    <rect x="8" y="11" width="1.2" height="12" class="accent"/>
    <text x="13" y="20.5" class="title">BAR CHART</text>
    <text x="15" y="51" class="tiny" font-weight="700">Income Analysis</text>
    <text x="15" y="56" class="fine">Pro every 4 minutes, assured, we</text>
    <text x="15" y="59.5" class="fine">get 3 phone calls. Suitable for all</text>
    <text x="15" y="63" class="fine">categories business and personal</text>
    <text x="15" y="66.5" class="fine">presentation, eaque ipsa quae ab</text>
    <text x="15" y="70" class="fine">illo inventore veritatis et quasi.</text>
    <text x="15" y="75" class="fine">Lorem ipsum dolor sit amet, elit</text>
    <text x="15" y="78.5" class="fine">sed do eiusmod tempor incididunt</text>
    <g>
      <rect x="100" y="44" width="10" height="82" rx="5" fill="#e2e2e2"/><rect x="100" y="96" width="10" height="30" rx="5" class="grey"/>
      <circle cx="105" cy="97" r="6" fill="#777"/><text x="105" y="98" text-anchor="middle" class="fine-w">Lowest</text>
      <rect x="122" y="44" width="10" height="82" rx="5" fill="#e2e2e2"/><rect x="122" y="86" width="10" height="40" rx="5" fill="#c4c4c4"/>
      <rect x="144" y="44" width="10" height="82" rx="5" fill="#e2e2e2"/><rect x="144" y="76" width="10" height="50" rx="5" fill="#c4c4c4"/>
      <rect x="166" y="44" width="10" height="82" rx="5" fill="#e2e2e2"/><rect x="166" y="72" width="10" height="54" rx="5" fill="#c4c4c4"/>
      <rect x="188" y="44" width="10" height="82" rx="5" fill="#e2e2e2"/><rect x="188" y="64" width="10" height="62" rx="5" fill="#bdbdbd"/>
      <rect x="210" y="44" width="10" height="82" rx="5" fill="#e2e2e2"/><rect x="210" y="70" width="10" height="56" rx="5" fill="#bdbdbd"/>
      <rect x="232" y="44" width="10" height="82" rx="5" class="ink"/>
      <circle cx="237" cy="41" r="6" class="ink"/><text x="237" y="42" text-anchor="middle" class="fine-w">Highest</text>
      <rect x="254" y="44" width="10" height="82" rx="5" class="accent"/>
      <circle cx="259" cy="41" r="6" class="accent"/><text x="259" y="42" text-anchor="middle" class="fine-w">Peak</text>
      <text x="105" y="132" text-anchor="middle" class="fine">2011</text><text x="127" y="132" text-anchor="middle" class="fine">2012</text>
      <text x="149" y="132" text-anchor="middle" class="fine">2013</text><text x="171" y="132" text-anchor="middle" class="fine">2014</text>
      <text x="193" y="132" text-anchor="middle" class="fine">2015</text><text x="215" y="132" text-anchor="middle" class="fine">2016</text>
      <text x="237" y="132" text-anchor="middle" class="fine">2017</text><text x="259" y="132" text-anchor="middle" class="fine">2018</text>
    </g>
    <rect y="160" width="296" height="6" class="ink"/><circle cx="6" cy="163" r="2.4" class="accent"/>
    <text x="11" y="164" class="foot-text">© Copyright 2018 KVTF. All rights reserved</text>
  </svg>
</section>

<section class="slide c3 r4" aria-label="Comparison by gender slide">
  <svg viewBox="0 0 296 166">
    <defs>
      <pattern id="tally-dark" width="4" height="8" patternUnits="userSpaceOnUse"><rect width="4" height="8" fill="#3a3a3a"/><rect x="1.3" y="1.5" width="1.4" height="5" rx=".6" fill="#fff"/></pattern>
      <pattern id="tally-red" width="4" height="8" patternUnits="userSpaceOnUse"><rect width="4" height="8" fill="#e9b9ba"/><rect x="1.3" y="1.5" width="1.4" height="5" rx=".6" fill="#fff"/></pattern>
    </defs>
    <rect x="8" y="11" width="1.2" height="12" class="accent"/>
    <text x="13" y="20.5" class="title">COMPARISON GENDER</text>
    <g class="rows">
      <text x="58" y="49" text-anchor="end" class="fine">23k</text><rect x="62" y="43" width="56" height="8" fill="url(#tally-dark)"/>
      <rect x="123" y="43" width="54" height="8" class="ink"/><text x="150" y="48" text-anchor="middle" class="label-w">Graphic Design</text>
      <rect x="182" y="43" width="56" height="8" fill="url(#tally-dark)"/><text x="242" y="49" class="fine">27k</text>

      <text x="58" y="66" text-anchor="end" class="fine">39k</text><rect x="62" y="60" width="56" height="8" fill="url(#tally-red)"/>
      <rect x="123" y="60" width="54" height="8" class="accent"/><text x="150" y="65" text-anchor="middle" class="label-w">Web Design</text>
      <rect x="182" y="60" width="56" height="8" fill="url(#tally-red)"/><text x="242" y="66" class="fine">15k</text>

      <text x="58" y="83" text-anchor="end" class="fine">29k</text><rect x="62" y="77" width="56" height="8" fill="url(#tally-dark)"/>
      <rect x="123" y="77" width="54" height="8" class="grey"/><text x="150" y="82" text-anchor="middle" class="label-w">SEO Analysis</text>
      <rect x="182" y="77" width="56" height="8" fill="url(#tally-dark)"/><text x="242" y="83" class="fine">32k</text>

      <text x="58" y="100" text-anchor="end" class="fine">29k</text><rect x="62" y="94" width="56" height="8" fill="url(#tally-dark)"/>
      <rect x="123" y="94" width="54" height="8" class="ink"/><text x="150" y="99" text-anchor="middle" class="label-w">Marketing</text>
      <rect x="182" y="94" width="56" height="8" fill="url(#tally-dark)"/><text x="242" y="100" class="fine">19k</text>

      <text x="58" y="117" text-anchor="end" class="fine">17k</text><rect x="62" y="111" width="56" height="8" fill="url(#tally-red)"/>
      <rect x="123" y="111" width="54" height="8" class="accent"/><text x="150" y="116" text-anchor="middle" class="label-w">Promotion</text>
      <rect x="182" y="111" width="56" height="8" fill="url(#tally-red)"/><text x="242" y="117" class="fine">21k</text>

      <text x="58" y="134" text-anchor="end" class="fine">11k</text><rect x="62" y="128" width="56" height="8" fill="url(#tally-dark)"/>
      <rect x="123" y="128" width="54" height="8" class="grey"/><text x="150" y="133" text-anchor="middle" class="label-w">Writing</text>
      <rect x="182" y="128" width="56" height="8" fill="url(#tally-dark)"/><text x="242" y="134" class="fine">18k</text>
    </g>
    <rect y="160" width="296" height="6" class="ink"/><circle cx="6" cy="163" r="2.4" class="accent"/>
    <text x="11" y="164" class="foot-text">© Copyright 2018 KVTF. All rights reserved</text>
  </svg>
</section>

<!-- Row 5 -->
<section class="slide c1 r5" aria-label="Arrow diagram slide">
  <svg viewBox="0 0 296 166">
    <rect x="8" y="11" width="1.2" height="12" class="accent"/>
    <text x="13" y="20.5" class="title">ARROW DIAGRAM</text>
    <polygon points="255,42 258,35 262,42" class="grey"/>
    <polygon points="230,58 258,30 258,52 215,95 185,95" class="grey" opacity=".0"/>
    <polygon points="258,35 262,72 248,62 212,98 190,76 226,40 212,30" fill="#808080"/>
    <polygon points="100,40 130,70 100,100 70,70" class="accent"/>
    <polygon points="160,40 190,70 160,100 130,70" class="ink"/>
    <polygon points="70,70 100,100 70,130 40,100" class="ink"/>
    <polygon points="130,70 160,100 130,130 100,100" class="grey"/>
    <polygon points="190,70 220,100 190,130 160,100" class="accent"/>
    <text x="100" y="70" text-anchor="middle" class="label-w" font-size="3">Visible Cost</text>
    <text x="100" y="74" text-anchor="middle" class="fine-w">Suitable for all category</text>
    <text x="160" y="70" text-anchor="middle" class="label-w" font-size="3">Visible Cost</text>
    <text x="160" y="74" text-anchor="middle" class="fine-w">Suitable for all category</text>
    <text x="232" y="60" text-anchor="middle" class="label-w" font-size="3">Visible Cost</text>
    <text x="70" y="100" text-anchor="middle" class="label-w" font-size="3">Visible Cost</text>
    <text x="70" y="104" text-anchor="middle" class="fine-w">Suitable for all category</text>
    <text x="130" y="100" text-anchor="middle" class="label-w" font-size="3">Visible Cost</text>
    <text x="130" y="104" text-anchor="middle" class="fine-w">Suitable for all category</text>
    <text x="190" y="100" text-anchor="middle" class="label-w" font-size="3">Visible Cost</text>
    <text x="190" y="104" text-anchor="middle" class="fine-w">Suitable for all category</text>
    <rect y="160" width="296" height="6" class="ink"/><circle cx="6" cy="163" r="2.4" class="accent"/>
    <text x="11" y="164" class="foot-text">© Copyright 2018 KVTF. All rights reserved</text>
  </svg>
</section>

<section class="slide c2 r5" aria-label="Investment infographic slide">
  <svg viewBox="0 0 296 166">
    <defs>
      <pattern id="blocks" width="12" height="12" patternUnits="userSpaceOnUse"><rect x="1" y="1" width="10" height="10" rx="1.5" fill="#1e1e1e"/></pattern>
      <pattern id="blocks-grey" width="12" height="12" patternUnits="userSpaceOnUse"><rect x="1" y="1" width="10" height="10" rx="1.5" fill="#777"/></pattern>
    </defs>
    <rect x="8" y="11" width="1.2" height="12" class="accent"/>
    <text x="13" y="20.5" class="title">INVESTMENT INFOGRAPHIC</text>
    <text x="30" y="60" font-size="15" class="ink">75%</text>
    <rect x="78" y="42" width="72" height="24" fill="url(#blocks)"/>
    <rect x="138" y="54" width="12" height="12" fill="#fff"/><rect x="139" y="55" width="10" height="10" rx="1.5" class="grey"/>
    <text x="190" y="52" font-size="10" class="ink">2017</text>
    <text x="218" y="52" class="fine">Our Sales</text>
    <text x="190" y="58" class="fine">This is just a sample, feel free to edit text, you may also add your</text>
    <text x="190" y="61" class="fine">own information for all categories and personal presentation.</text>
    <text x="30" y="97" font-size="15" class="grey">80%</text>
    <rect x="78" y="79" width="72" height="24" fill="url(#blocks-grey)"/>
    <text x="190" y="88" font-size="10" class="grey">2018</text>
    <text x="218" y="88" class="fine">Our Sales</text>
    <text x="190" y="94" class="fine">This is just a sample, feel free to edit text, you may also add your</text>
    <text x="190" y="97" class="fine">own information for all categories and personal presentation.</text>
    <line x1="25" y1="112" x2="275" y2="112" stroke="#ccc" stroke-width=".5"/>
    <path d="M42 122 L68 122 L70 138 L40 138 Z" class="grey"/>
    <path d="M49 122 Q55 115 61 122" fill="none" stroke="#777" stroke-width="1"/>
    <text x="55" y="134" text-anchor="middle" font-size="8" fill="#fff">$27</text>
    <text x="80" y="124" class="tiny" font-weight="700">Income Analysis</text>
    <text x="80" y="129" class="fine">Pro every 4 minutes assured, we get 3 phone calls. Suitable for all categories business and personal presentation, suitable for all</text>
    <text x="80" y="132.5" class="fine">categories business and personal presentation, eaque ipsa quae ab illo inventore veritatis et quasi architecto beatae.</text>
    <rect y="160" width="296" height="6" class="ink"/><circle cx="6" cy="163" r="2.4" class="accent"/>
    <text x="11" y="164" class="foot-text">© Copyright 2018 KVTF. All rights reserved</text>
  </svg>
</section>

<section class="slide c3 r5" aria-label="Shopping bag infographic slide">
  <svg viewBox="0 0 296 166">
    <rect x="8" y="11" width="1.2" height="12" class="accent"/>
    <text x="13" y="20.5" class="title">SHOPPING BAG INFOGRAPHIC</text>
    <g>
      <text x="43" y="110" text-anchor="middle" font-size="8" class="ink">$9M</text>
      <rect x="30" y="113" width="26" height="12" class="ink"/>
      <path d="M38 115 Q43 119 48 115" fill="none" stroke="#fff" stroke-width=".5"/>
      <rect x="30" y="125" width="26" height="8" class="ink"/><text x="43" y="130.5" text-anchor="middle" class="label-w" font-size="3">Description</text>
      <text x="73" y="92" text-anchor="middle" font-size="8" class="accent">$17M</text>
      <rect x="60" y="95" width="26" height="30" class="accent"/>
      <path d="M68 97 Q73 101 78 97" fill="none" stroke="#fff" stroke-width=".5"/>
      <rect x="60" y="125" width="26" height="8" class="accent"/><text x="73" y="130.5" text-anchor="middle" class="label-w" font-size="3">Description</text>
      <text x="103" y="75" text-anchor="middle" font-size="8" class="grey">$25M</text>
      <rect x="90" y="78" width="26" height="47" class="grey"/>
      <path d="M98 80 Q103 84 108 80" fill="none" stroke="#fff" stroke-width=".5"/>
      <rect x="90" y="125" width="26" height="8" class="grey"/><text x="103" y="130.5" text-anchor="middle" class="label-w" font-size="3">Description</text>
      <text x="133" y="50" text-anchor="middle" font-size="8" class="ink">$32M</text>
      <rect x="120" y="53" width="26" height="72" class="ink"/>
      <path d="M128 55 Q133 59 138 55" fill="none" stroke="#fff" stroke-width=".5"/>
      <rect x="120" y="125" width="26" height="8" class="ink"/><text x="133" y="130.5" text-anchor="middle" class="label-w" font-size="3">Description</text>
    </g>
    <g>
      <circle cx="192" cy="52" r="6" class="ink"/><rect x="189.5" y="50.5" width="5" height="3.5" fill="#fff"/>
      <text x="202" y="50" class="tiny">Description</text>
      <text x="202" y="54" class="fine">Pro every 4 minutes assured, we</text><text x="202" y="57" class="fine">get 3 phone calls</text>
      <circle cx="192" cy="77" r="6" class="accent"/><path d="M189 77 Q192 73 195 77 Z" fill="#fff"/>
      <text x="202" y="75" class="tiny" style="fill:var(--red)">Description</text>
      <text x="202" y="79" class="fine">Pro every 4 minutes assured, we</text><text x="202" y="82" class="fine">get 3 phone calls</text>
      <circle cx="192" cy="102" r="6" class="grey"/><rect x="189.5" y="100.5" width="5" height="3" fill="#fff"/>
      <text x="202" y="100" class="tiny">Description</text>
      <text x="202" y="104" class="fine">Pro every 4 minutes assured, we</text><text x="202" y="107" class="fine">get 3 phone calls</text>
      <circle cx="192" cy="127" r="6" class="ink"/><rect x="189" y="125.5" width="4.5" height="3" fill="#fff"/><polygon points="193.5,127 196,125.5 196,128.5" fill="#fff"/>
      <text x="202" y="125" class="tiny">Description</text>
      <text x="202" y="129" class="fine">Pro every 4 minutes assured, we</text><text x="202" y="132" class="fine">get 3 phone calls</text>
    </g>
    <rect y="160" width="296" height="6" class="ink"/><circle cx="6" cy="163" r="2.4" class="accent"/>
    <text x="11" y="164" class="foot-text">© Copyright 2018 KVTF. All rights reserved</text>
  </svg>
</section>

<!-- Row 6 -->
<section class="slide c1 r6" aria-label="Basic chevron process slide">
  <svg viewBox="0 0 296 166">
    <rect x="8" y="11" width="1.2" height="12" class="accent"/>
    <text x="13" y="20.5" class="title">BASIC CHEVRON PROCESS</text>
    <polygon points="24,78 78,78 82,82 78,86 24,86 28,82" class="ink"/>
    <polygon points="80,78 130,78 134,82 130,86 80,86 84,82" class="accent"/>
    <polygon points="132,78 182,78 186,82 182,86 132,86 136,82" class="grey"/>
    <polygon points="184,78 234,78 238,82 234,86 184,86 188,82" class="ink"/>
    <polygon points="236,78 280,78 284,82 280,86 236,86 240,82" class="accent"/>
    <line x1="50" y1="66" x2="50" y2="78" stroke="#999" stroke-width=".4"/>
    <circle cx="50" cy="62" r="6.5" class="ink"/><path d="M47.5 64.5 L52.5 59.5" stroke="#fff" stroke-width=".9"/>
    <line x1="148" y1="66" x2="148" y2="78" stroke="#999" stroke-width=".4"/>
    <circle cx="148" cy="62" r="6.5" class="grey"/><rect x="145.5" y="60" width="5" height="4" fill="none" stroke="#fff" stroke-width=".6"/>
    <line x1="246" y1="66" x2="246" y2="78" stroke="#999" stroke-width=".4"/>
    <circle cx="246" cy="62" r="6.5" class="accent"/><rect x="243.5" y="60" width="5" height="4" fill="none" stroke="#fff" stroke-width=".6"/>
    <line x1="100" y1="86" x2="100" y2="96" stroke="#999" stroke-width=".4"/>
    <circle cx="100" cy="101" r="6.5" class="accent"/><rect x="97.5" y="99" width="1" height="4" fill="#fff"/><rect x="99.5" y="98" width="1" height="5" fill="#fff"/><rect x="101.5" y="100" width="1" height="3" fill="#fff"/>
    <line x1="196" y1="86" x2="196" y2="96" stroke="#999" stroke-width=".4"/>
    <circle cx="196" cy="101" r="6.5" class="ink"/><circle cx="196" cy="101" r="2.4" fill="none" stroke="#fff" stroke-width=".7"/>
    <text x="100" y="54" text-anchor="middle" class="tiny" style="fill:var(--red)">Idea</text>
    <text x="100" y="58" text-anchor="middle" class="fine">Suitable for all level business and</text>
    <text x="100" y="61" text-anchor="middle" class="fine">personal presentation, feel free</text>
    <text x="196" y="54" text-anchor="middle" class="tiny">Brainstorming</text>
    <text x="196" y="58" text-anchor="middle" class="fine">Suitable for all level business and</text>
    <text x="196" y="61" text-anchor="middle" class="fine">personal presentation, feel free</text>
    <text x="50" y="96" text-anchor="middle" class="tiny">Research</text>
    <text x="50" y="100" text-anchor="middle" class="fine">Suitable for all level business</text>
    <text x="50" y="103" text-anchor="middle" class="fine">and personal presentation</text>
    <text x="148" y="96" text-anchor="middle" class="tiny">Search</text>
    <text x="148" y="100" text-anchor="middle" class="fine">Suitable for all level business</text>
    <text x="148" y="103" text-anchor="middle" class="fine">and personal presentation</text>
    <text x="246" y="96" text-anchor="middle" class="tiny">Strategy</text>
    <text x="246" y="100" text-anchor="middle" class="fine">Suitable for all level business</text>
    <text x="246" y="103" text-anchor="middle" class="fine">and personal presentation</text>
    <rect y="160" width="296" height="6" class="ink"/><circle cx="6" cy="163" r="2.4" class="accent"/>
    <text x="11" y="164" class="foot-text">© Copyright 2018 KVTF. All rights reserved</text>
  </svg>
</section>

<section class="slide c2 r6" aria-label="PESTEL analysis slide">
  <svg viewBox="0 0 296 166">
    <rect x="8" y="11" width="1.2" height="12" class="accent"/>
    <text x="13" y="20.5" class="title">PESTEL ANALYSIS</text>
    <g>
      <polygon points="32,84 42,67 62,67 72,84 62,101 42,101" class="ink"/>
      <polygon points="69,102 79,85 99,85 109,102 99,119 79,119" class="grey"/>
      <polygon points="106,84 116,67 136,67 146,84 136,101 116,101" class="accent"/>
      <polygon points="143,102 153,85 173,85 183,102 173,119 153,119" class="accent"/>
      <polygon points="180,84 190,67 210,67 220,84 210,101 190,101" class="grey"/>
      <polygon points="217,102 227,85 247,85 257,102 247,119 227,119" class="ink"/>
      <text x="52" y="90" text-anchor="middle" class="label-w">Politics</text>
      <text x="89" y="108" text-anchor="middle" class="label-w">Economy</text>
      <text x="126" y="90" text-anchor="middle" class="label-w">Social</text>
      <text x="163" y="108" text-anchor="middle" class="label-w">Technology</text>
      <text x="200" y="90" text-anchor="middle" class="label-w">Environment</text>
      <text x="237" y="108" text-anchor="middle" class="label-w">Legal</text>
      <rect x="49" y="77" width="6" height="4" fill="none" stroke="#fff" stroke-width=".6"/>
      <circle cx="126" cy="78" r="2.3" fill="#fff"/>
      <circle cx="200" cy="78" r="2.3" fill="#fff"/>
      <path d="M86 96 L92 96 M89 93 L89 99" stroke="#fff" stroke-width=".8"/>
      <path d="M163 92 L163 99" stroke="#fff" stroke-width=".9"/>
      <path d="M233 95 L241 95 M237 93 L237 99" stroke="#fff" stroke-width=".7"/>
      <line x1="52" y1="67" x2="52" y2="55" stroke="#999" stroke-width=".3"/>
      <line x1="126" y1="67" x2="126" y2="55" stroke="#999" stroke-width=".3"/>
      <line x1="200" y1="67" x2="200" y2="55" stroke="#999" stroke-width=".3"/>
      <line x1="89" y1="119" x2="89" y2="130" stroke="#999" stroke-width=".3"/>
      <line x1="163" y1="119" x2="163" y2="130" stroke="#999" stroke-width=".3"/>
      <line x1="237" y1="119" x2="237" y2="130" stroke="#999" stroke-width=".3"/>
      <text x="75" y="49" text-anchor="middle" class="fine">Suitable for all level corporate</text><text x="75" y="52" text-anchor="middle" class="fine">business and personal presentation</text>
      <text x="149" y="49" text-anchor="middle" class="fine">Suitable for all level corporate</text><text x="149" y="52" text-anchor="middle" class="fine">business and personal presentation</text>
      <text x="223" y="49" text-anchor="middle" class="fine">Suitable for all level corporate</text><text x="223" y="52" text-anchor="middle" class="fine">business and personal presentation</text>
      <text x="66" y="134" text-anchor="middle" class="fine">Suitable for all level corporate</text><text x="66" y="137" text-anchor="middle" class="fine">business and personal presentation</text>
      <text x="140" y="134" text-anchor="middle" class="fine">Suitable for all level corporate</text><text x="140" y="137" text-anchor="middle" class="fine">business and personal presentation</text>
      <text x="214" y="134" text-anchor="middle" class="fine">Suitable for all level corporate</text><text x="214" y="137" text-anchor="middle" class="fine">business and personal presentation</text>
    </g>
    <rect y="160" width="296" height="6" class="ink"/><circle cx="6" cy="163" r="2.4" class="accent"/>
    <text x="11" y="164" class="foot-text">© Copyright 2018 KVTF. All rights reserved</text>
  </svg>
</section>

<section class="slide c3 r6" aria-label="Three steps slide">
  <svg viewBox="0 0 296 166">
    <rect x="8" y="11" width="1.2" height="12" class="accent"/>
    <text x="13" y="20.5" class="title">THREE STEPS</text>
    <g>
      <circle cx="26" cy="51" r="5" class="ink"/><rect x="24" y="50" width="1" height="3" fill="#fff"/><rect x="26" y="48.5" width="1" height="4.5" fill="#fff"/><rect x="28" y="49.5" width="1" height="3.5" fill="#fff"/>
      <text x="40" y="51" class="tiny">Sample Text</text>
      <text x="40" y="56" class="fine">Lorem ipsum dolor sit amet, consectetur adipiscing elit. Duis ligula lorem,</text>
      <text x="40" y="59.5" class="fine">consequat eget, tristique nec, auctor quis, purus.</text>
      <circle cx="26" cy="81" r="5" class="accent"/><path d="M24 83 L28 79" stroke="#fff" stroke-width=".8"/>
      <text x="40" y="81" class="tiny" style="fill:var(--red)">Sample Text</text>
      <text x="40" y="86" class="fine">Lorem ipsum dolor sit amet, consectetur adipiscing elit. Duis ligula lorem,</text>
      <text x="40" y="89.5" class="fine">consequat eget, tristique nec, auctor quis, purus.</text>
      <circle cx="26" cy="111" r="5" class="grey"/><circle cx="25.4" cy="110.4" r="1.6" fill="none" stroke="#fff" stroke-width=".6"/>
      <text x="40" y="111" class="tiny">Sample Text</text>
      <text x="40" y="116" class="fine">Lorem ipsum dolor sit amet, consectetur adipiscing elit. Duis ligula lorem,</text>
      <text x="40" y="119.5" class="fine">consequat eget, tristique nec, auctor quis, purus.</text>
    </g>
    <g fill="none" stroke-width="10">
      <circle cx="243" cy="58" r="20" stroke="#1e1e1e"/>
      <circle cx="243" cy="112" r="20" stroke="#7b7b7b"/>
      <circle cx="213" cy="85" r="20" stroke="#a30d12"/>
    </g>
    <path d="M206 90 L210 84 L214 87 L219 81" fill="none" stroke="#a30d12" stroke-width=".8"/>
    <rect x="238" y="55" width="10" height="5" rx="2" fill="none" stroke="#555" stroke-width=".6"/>
    <rect x="239" y="108" width="8" height="7" fill="none" stroke="#888" stroke-width=".6"/>
    <rect y="160" width="296" height="6" class="ink"/><circle cx="6" cy="163" r="2.4" class="accent"/>
    <text x="11" y="164" class="foot-text">© Copyright 2018 KVTF. All rights reserved</text>
  </svg>
</section>

<!-- Row 7 -->
<section class="slide c1 r7" aria-label="Project timeline slide">
  <svg viewBox="0 0 296 166">
    <rect x="8" y="11" width="1.2" height="12" class="accent"/>
    <text x="13" y="20.5" class="title">PROJECT TIMELINE</text>
    <g class="months" text-anchor="middle">
      <text x="48" y="41" class="fine">Project step</text>
      <text x="93" y="41" class="fine">Jan</text><text x="109" y="41" class="fine">Feb</text><text x="125" y="41" class="fine">Mar</text>
      <text x="141" y="41" class="fine">Apr</text><text x="157" y="41" class="fine">May</text><text x="173" y="41" class="fine">June</text>
      <text x="189" y="41" class="fine">July</text><text x="205" y="41" class="fine">Aug</text><text x="221" y="41" class="fine">Sep</text>
      <text x="237" y="41" class="fine">Oct</text><text x="253" y="41" class="fine">Nov</text><text x="269" y="41" class="fine">Dec</text>
    </g>
    <g stroke="#ddd" stroke-width=".3">
      <line x1="40" y1="44" x2="277" y2="44"/><line x1="40" y1="53" x2="277" y2="53"/><line x1="40" y1="62" x2="277" y2="62"/>
      <line x1="40" y1="71" x2="277" y2="71"/><line x1="40" y1="80" x2="277" y2="80"/><line x1="40" y1="89" x2="277" y2="89"/>
      <line x1="40" y1="98" x2="277" y2="98"/><line x1="40" y1="107" x2="277" y2="107"/><line x1="40" y1="116" x2="277" y2="116"/>
      <line x1="40" y1="125" x2="277" y2="125"/>
    </g>
    <g class="phase-labels">
      <text x="46" y="49.5" class="fine">Phases 01</text><text x="46" y="58.5" class="fine">Phases 02</text><text x="46" y="67.5" class="fine">Phases 03</text>
      <text x="46" y="76.5" class="fine">Phases 04</text><text x="46" y="85.5" class="fine">Phases 05</text><text x="46" y="94.5" class="fine">Phases 06</text>
      <text x="46" y="103.5" class="fine">Phases 07</text><text x="46" y="112.5" class="fine">Phases 08</text><text x="46" y="121.5" class="fine">Phases 09</text>
    </g>
    <g stroke-width="4" stroke-linecap="round">
      <line x1="93" y1="48.5" x2="118" y2="48.5" stroke="#1e1e1e"/>
      <line x1="232" y1="48.5" x2="270" y2="48.5" stroke="#a30d12"/>
      <line x1="113" y1="57.5" x2="126" y2="57.5" stroke="#1e1e1e"/><line x1="160" y1="57.5" x2="180" y2="57.5" stroke="#1e1e1e"/><line x1="234" y1="57.5" x2="258" y2="57.5" stroke="#7b7b7b"/>
      <line x1="126" y1="66.5" x2="190" y2="66.5" stroke="#a30d12"/>
      <line x1="149" y1="75.5" x2="173" y2="75.5" stroke="#1e1e1e"/><line x1="209" y1="75.5" x2="228" y2="75.5" stroke="#a30d12"/>
      <line x1="191" y1="84.5" x2="270" y2="84.5" stroke="#7b7b7b"/>
      <line x1="131" y1="93.5" x2="162" y2="93.5" stroke="#1e1e1e"/>
      <line x1="108" y1="102.5" x2="157" y2="102.5" stroke="#a30d12"/><line x1="204" y1="102.5" x2="220" y2="102.5" stroke="#1e1e1e"/>
      <line x1="233" y1="111.5" x2="258" y2="111.5" stroke="#1e1e1e"/>
      <line x1="225" y1="120.5" x2="258" y2="120.5" stroke="#a30d12"/>
    </g>
    <text x="60" y="134" class="fine">●  Description</text>
    <text x="98" y="134" class="fine" style="fill:var(--red)">●  Description</text>
    <text x="136" y="134" class="fine">●  Description</text>
    <text x="174" y="134" class="fine">●  Description</text>
    <text x="212" y="134" class="fine" style="fill:var(--red)">●  Description</text>
    <rect y="160" width="296" height="6" class="ink"/><circle cx="6" cy="163" r="2.4" class="accent"/>
    <text x="11" y="164" class="foot-text">© Copyright 2018 KVTF. All rights reserved</text>
  </svg>
</section>

<section class="slide c2 r7" aria-label="Three bullets area slide">
  <svg viewBox="0 0 296 166">
    <defs><linearGradient id="facadephoto" x1="0" y1="0" x2="0" y2="1"><stop offset="0" stop-color="#4a4a4a"/><stop offset=".5" stop-color="#d2d2d2"/><stop offset="1" stop-color="#3a3a3a"/></linearGradient></defs>
    <rect x="8" y="11" width="1.2" height="12" class="accent"/>
    <text x="13" y="20.5" class="title">THREE BULLETS AREA</text>
    <rect x="0" y="27" width="296" height="63" fill="url(#facadephoto)" role="img" aria-label="Black and white photo of a building facade"/>
    <polygon points="50,96 60,79 80,79 90,96 80,113 60,113" class="ink"/>
    <circle cx="66" cy="96" r="1.4" fill="#fff"/><circle cx="74" cy="92" r="1.4" fill="#fff"/><circle cx="74" cy="100" r="1.4" fill="#fff"/>
    <path d="M66 96 L74 92 M66 96 L74 100" stroke="#fff" stroke-width=".6"/>
    <polygon points="128,96 138,79 158,79 168,96 158,113 138,113" class="accent"/>
    <path d="M141 93 L148 89 L155 93 L148 97 Z M141 97 L148 101 L155 97" fill="none" stroke="#fff" stroke-width=".7"/>
    <polygon points="206,96 216,79 236,79 246,96 236,113 216,113" class="grey"/>
    <path d="M222 103 L230 103 L228 90 L224 90 Z" fill="#fff"/>
    <text x="70" y="121" text-anchor="middle" class="fine">Lorem ipsum dolor sit amet,</text>
    <text x="70" y="124.5" text-anchor="middle" class="fine">consectetur adipiscing elit, sed do</text>
    <text x="70" y="128" text-anchor="middle" class="fine">eiusmod tempor incididunt ut labore</text>
    <text x="148" y="121" text-anchor="middle" class="fine">Lorem ipsum dolor sit amet,</text>
    <text x="148" y="124.5" text-anchor="middle" class="fine">consectetur adipiscing elit, sed do</text>
    <text x="148" y="128" text-anchor="middle" class="fine">eiusmod tempor incididunt ut labore</text>
    <text x="226" y="121" text-anchor="middle" class="fine">Lorem ipsum dolor sit amet,</text>
    <text x="226" y="124.5" text-anchor="middle" class="fine">consectetur adipiscing elit, sed do</text>
    <text x="226" y="128" text-anchor="middle" class="fine">eiusmod tempor incididunt ut labore</text>
    <rect y="160" width="296" height="6" class="ink"/><circle cx="6" cy="163" r="2.4" class="accent"/>
    <text x="11" y="164" class="foot-text">© Copyright 2018 KVTF. All rights reserved</text>
  </svg>
</section>

<section class="slide c3 r7" aria-label="Thank you slide">
  <svg viewBox="0 0 296 166">
    <defs><radialGradient id="closingphoto" cx=".3" cy=".4" r=".8"><stop offset="0" stop-color="#3a332c"/><stop offset="1" stop-color="#121110"/></radialGradient></defs>
    <rect width="296" height="166" fill="url(#closingphoto)" role="img" aria-label="Dim background photo of a military scene"/>
    <circle cx="48" cy="86" r="6" class="accent"/>
    <text x="58" y="90" font-size="12" fill="#fff">KVTF</text>
    <text x="162" y="70" font-size="13" fill="#fff" letter-spacing=".5">THANK YOU</text>
    <g fill="#fff">
      <path d="M163 80 L166 77.5 L169 80 L168 80 L168 82.5 L164 82.5 L164 80 Z"/>
      <text x="174" y="80" class="fine-w">123 Street Road</text>
      <text x="174" y="83" class="fine-w">City 12345</text>
      <rect x="164" y="88" width="3" height="4.5" rx=".8"/>
      <text x="174" y="91.5" class="fine-w">(123) 456-7890</text>
      <rect x="163.5" y="97" width="4.5" height="3.2"/>
      <text x="174" y="100" class="fine-w">email@kvtf-example.com</text>
      <circle cx="166" cy="107" r="2.2" fill="none" stroke="#fff" stroke-width=".5"/>
      <text x="174" y="108.5" class="fine-w">www.kvtf-example.com</text>
    </g>
  </svg>
</section>

</main>
</body>
</html>
```